UI Redesign For Mobile Events iPhone App

We need a new UI design for our Social Events mobile app. Our app called Vessa is geared to help users find trending events in their local area. We show visual metrics on percent full and male female ratio and age group ratings. We want people to see whats going on at event before they get there through our app. Also we have a group chat portion to our app that we need included in the design. We would like to see a fresh, clean, and easy to use user interface that uses colors like, purple, blue and or hot pink.You may visit our website myvessa.example for more information about what our app is geared to do.
Updates

Target Market(s)

Our target market people that use social networks and attend social events ranging from ages 16-44.

Industry/Entity Type

Events

Requirements
Must have
• We would like to see an Example layout of all screens. (UPDATE: Please use our current background in your design, A PSD has been uploaded for you to grab the background. The Vessa Logo is NOT required to be included at the top of every screen)

-Profile Screen: Shows points earned, events attending, events created
-Event Listings Screen: Must have large image for event, visual metrics, date& time, location, attend button, invite friends button, Label for user who created the event
-Event Description Page: Shows everything as the event listing, has a description of the event, shows friends that are attending, points available
-Group Messaging Screen
-Slide Out Navigation Screen
-Notification Screen
-Ticket Screen
-Friends Activity Screen
-Friends Profile View: Shows events they've attended and points they've earned under their contact picture; invite button
-Sign-In Screen
-Register Screen

A way to label/categorize our different types of events:
-Nightlife
-Family
-Live Music & Concerts
-Restaurants
Group Chat Layout
Visual Meters for Percent Full, Male Female Ratio, Age Rating

```html
<!DOCTYPE html>
<html lang="en">
<head>
<meta charset="utf-8">
<title>Vessa – Categories</title>
<link rel="stylesheet" href="https://fonts.googleapis.com/css2?family=Ubuntu:wght@300;400&display=swap">
<style>
  :root {
    --page-bg: #ecebe8;
    --purple: #8c42b3;
    --purple-line: #7a379e;
    --blue: #1ca6de;
    --tabbar: #6e2d93;
    --tab-active: #55206f;
    --tab-divider: #5f2581;
    --family-fill: #cfa9dc;
    --white: #ffffff;
  }
  * { box-sizing: border-box; margin: 0; padding: 0; }
  html, body {
    width: 1200px;
    height: 1080px;
    overflow: hidden;
    background: var(--page-bg);
    font-family: "Ubuntu", "Helvetica Neue", Arial, sans-serif;
  }
  .app-screen {
    position: absolute;
    left: 320px;
    top: 43px;
    width: 560px;
    height: 994px;
    background: var(--purple);
    display: flex;
    flex-direction: column;
    overflow: hidden;
    box-shadow: 0 6px 30px rgba(0,0,0,0.12);
  }
  .category-list { list-style: none; flex: 1; display: flex; flex-direction: column; }
  .category {
    flex: 1;
    display: flex;
    align-items: center;
    padding-left: 44px;
    background: var(--purple);
    border-bottom: 2px solid var(--purple-line);
    color: var(--white);
  }
  .category:last-child { border-bottom: none; }
  .category--active { background: var(--blue); border-bottom-color: var(--blue); }
  .category__icon { width: 66px; height: 82px; flex: none; }
  .category__label {
    margin-left: 26px;
    font-weight: 300;
    font-size: 31px;
    line-height: 1;
    white-space: nowrap;
  }
  .family-icon {
    width: 66px;
    height: 56px;
    flex: none;
    border-radius: 6px;
    background: var(--family-fill);
  }
  .tab-bar {
    height: 96px;
    display: flex;
    background: var(--tabbar);
    border-top: 2px solid var(--purple-line);
  }
  .tab {
    flex: 1;
    display: flex;
    flex-direction: column;
    align-items: center;
    justify-content: center;
    gap: 4px;
    color: var(--white);
    font-size: 13px;
    font-weight: 400;
    line-height: 1;
    border-right: 1px solid var(--tab-divider);
  }
  .tab:last-child { border-right: none; }
  .tab--settings { background: var(--tab-active); }
  .tab__icon { width: 36px; height: 36px; }
  .brand-dot {
    width: 28px; height: 28px; margin: 4px;
    border-radius: 50%;
    border: 2px solid var(--white);
  }
</style>
</head>
<body>
  <main class="app-screen">
    <ul class="category-list">
      <li class="category">
        <svg class="category__icon" viewBox="0 0 62 78" fill="none" stroke="#fff" stroke-width="4" stroke-linecap="round">
          <path d="M10 6 V26 M18 6 V26 M26 6 V26 M8 26 Q18 38 28 26 M18 32 V72"/>
          <path d="M48 6 Q36 22 40 40 L46 40 V72"/>
        </svg>
        <span class="category__label">Restaurants</span>
      </li>
      <li class="category">
        <svg class="category__icon" viewBox="0 0 62 78" fill="none" stroke="#fff" stroke-width="4" stroke-linecap="round" stroke-linejoin="round">
          <path d="M6 12 H56 L31 42 Z" fill="#fff"/>
          <path d="M31 42 V66 M18 68 H44"/>
          <path d="M44 6 L38 16"/>
          <circle cx="53" cy="64" r="4" fill="#fff" stroke="none"/>
        </svg>
        <span class="category__label">Nightlife</span>
      </li>
      <li class="category category--active">
        <svg class="category__icon" viewBox="0 0 62 78" fill="none" stroke="#fff" stroke-width="4" stroke-linecap="round" stroke-linejoin="round">
          <rect x="26" y="4" width="18" height="30" rx="9" transform="rotate(20 35 19)"/>
          <path d="M26 32 L20 48"/>
          <path d="M20 48 Q6 54 14 62 Q24 70 12 76"/>
        </svg>
        <span class="category__label">Live concerts</span>
      </li>
      <li class="category">
        <div class="family-icon" role="img" aria-label="Family icon: parents with children"></div>
        <span class="category__label">Family</span>
      </li>
    </ul>

    <nav class="tab-bar">
      <div class="tab">
        <svg class="tab__icon" viewBox="0 0 40 40" fill="#fff">
          <circle cx="20" cy="13" r="9"/>
          <path d="M4 38 Q4 24 20 24 Q36 24 36 38 Z"/>
        </svg>
        <span>profile</span>
      </div>
      <div class="tab">
        <div class="brand-dot"></div>
        <span>my vessa</span>
      </div>
      <div class="tab">
        <svg class="tab__icon" viewBox="0 0 40 40" fill="none" stroke="#fff" stroke-width="2">
          <rect x="4" y="7" width="32" height="29" rx="2"/>
          <rect x="4" y="7" width="32" height="7" fill="#fff"/>
          <path d="M4 22 H36 M4 29 H36 M12 14 V36 M20 14 V36 M28 14 V36"/>
        </svg>
        <span>events</span>
      </div>
      <div class="tab">
        <svg class="tab__icon" viewBox="0 0 40 40" fill="#fff">
          <path d="M8 14 L24 4 L36 24 L20 34 Z"/>
          <path d="M14 26 L24 20" stroke="#6e2d93" stroke-width="2"/>
        </svg>
        <span>tickets</span>
      </div>
      <div class="tab tab--settings">
        <svg class="tab__icon" viewBox="0 0 40 40">
          <circle cx="20" cy="20" r="13" fill="none" stroke="#fff" stroke-width="7" stroke-dasharray="5.1 5.1"/>
          <circle cx="20" cy="20" r="10" fill="#fff"/>
          <circle cx="20" cy="20" r="4.5" fill="#55206f"/>
        </svg>
      </div>
    </nav>
  </main>
</body>
</html>
```